Volunteer fire fighters needed banner

As part of our recruitment campaign, we need a sign we can post on our sign trailer to entice locals to join our volunteer fire service. This design will be printed on a banner, front and back, to catch traffic going in both directions on a busy roadway. This banner will have a printed surface of 4 feet tall by 8 feet long.
Our fire department is looking to attract people between the ages of 18 and 35 years old who are interested in being a firefighter. We offer our volunteers:
-Free professional training
-All equipment supplied
-Tax abatements for active volunteers
For more information, you can check us out at:
Brackenmoorfire.example

This design should:
-scale to and fit a 4'x8' canvas
-Include our web address "BrackenMoorFire.example"
-Say "Members Wanted"
-"Drill every Tuesday at 7pm"
-"57 Kestrel Pond Lane"
-Include "Bracken Moor Fire Department"

We've included reference photos and past images we use for our other campaigns for inspiration for you.

Target Market(s)

18-35 y/o

Industry/Entity Type

Fire Service

Requirements
Must have
• -scale to and fit a 4'x8' canvas -Include our web address "BrackenMoorFire.example" -Say "Members Wanted" -"Drill every Tuesday at 7pm" -"57 Kestrel Pond Lane" -Include "Bracken Moor Fire Department"

```html
<!DOCTYPE html>
<html lang="en">
<head>
<meta charset="utf-8">
<title>Bracken Moor Fire Department – Recruitment Banner</title>
<link rel="stylesheet" href="https://fonts.googleapis.com/css2?family=Nunito:wght@800&family=Oswald:wght@700&family=Alfa+Slab+One&family=Roboto:wght@700;900&family=Arimo:ital,wght@0,400;1,700&display=swap">
<style>
  :root {
    --frame: #8886bc;
    --paper: #ffffff;
    --teal: #1f8f7a;
    --navy: #14105a;
    --plum: #6b0a57;
    --ink: #111111;
    --photo-red: #c8201e;
    --photo-grey: #b9b6b0;
  }
  * { margin: 0; padding: 0; box-sizing: border-box; }
  html, body { width: 1200px; height: 830px; overflow: hidden; background: var(--paper); }
  .canvas { position: relative; width: 1200px; height: 830px; background: var(--paper); }
  .banner-art { position: absolute; left: 0; top: 0; }
  .text { position: absolute; white-space: nowrap; line-height: 1; }

  .dept-mark {
    left: 496px; top: 228px; width: 118px;
    display: flex; flex-direction: column; align-items: center; gap: 8px;
    font-family: "Roboto", sans-serif; font-weight: 700; font-size: 17px;
    color: var(--navy); text-align: center; white-space: normal; line-height: 1.15;
  }
  .dept-mark .dot { width: 20px; height: 20px; border-radius: 50%; background: var(--navy); }

  .headline { font-family: "Nunito", sans-serif; font-weight: 800; color: var(--teal);
    text-shadow: 2px 2px 0 var(--navy); }
  .headline-top { left: 636px; top: 186px; display: flex; align-items: baseline; gap: 8px; }
  .headline-local { font-size: 40px; letter-spacing: -0.5px; }
  .headline-members { font-size: 56px; letter-spacing: -1px; }
  .headline-wanted { left: 746px; top: 234px; font-size: 92px; letter-spacing: -2px;
    text-shadow: 3px 3px 0 var(--navy); }

  .drill { left: 598px; top: 356px; font-family: "Oswald", sans-serif; font-weight: 700;
    font-size: 47px; letter-spacing: -0.5px; color: var(--teal); }
  .drill .strong { color: var(--navy); }

  .dept-name { left: 598px; top: 432px; width: 488px; text-align: center;
    font-family: "Alfa Slab One", serif; font-size: 38px; color: var(--plum); letter-spacing: 3px; }
  .dept-type { left: 598px; top: 478px; width: 488px; text-align: center;
    font-family: "Roboto", sans-serif; font-weight: 900; font-size: 31px; color: var(--ink); letter-spacing: 1px; }

  .address { left: 735px; top: 530px; font-family: "Arimo", sans-serif; font-size: 28px; color: var(--navy); }

  .web { left: 530px; top: 589px; width: 584px; text-align: center;
    font-family: "Arimo", sans-serif; font-style: italic; font-weight: 700;
    font-size: 37px; color: var(--paper); }
</style>
</head>
<body>
<main class="canvas">
  <svg class="banner-art" width="1200" height="830" viewBox="0 0 1200 830">
    <defs>
      <linearGradient id="photoTone" x1="0" y1="0" x2="1" y2="1">
        <stop offset="0" stop-color="#e8e4d6"/>
        <stop offset="0.35" stop-color="var(--photo-red)"/>
        <stop offset="0.7" stop-color="#a11614"/>
        <stop offset="1" stop-color="var(--photo-grey)"/>
      </linearGradient>
    </defs>
    <rect class="frame" x="104.5" y="166.5" width="1020" height="504" fill="none" stroke="var(--frame)" stroke-width="13"/>
    <polygon class="web-band" points="491,577 1118,577 1118,640 522,640" fill="var(--teal)"/>
    <polygon class="truck-photo" role="img" aria-label="Photo of a red fire engine parked in the station bay"
      points="111,173 329,173 576,664 111,664" fill="url(#photoTone)"/>
    <g class="pin-icon" fill="var(--navy)">
      <path d="M712 530c-6.1 0-11 4.9-11 11 0 8.3 11 19 11 19s11-10.7 11-19c0-6.1-4.9-11-11-11zm0 15.5a4.5 4.5 0 1 1 0-9 4.5 4.5 0 0 1 0 9z"/>
    </g>
  </svg>

  <div class="text dept-mark"><span class="dot"></span><span>Bracken Moor Fire Dept</span></div>

  <div class="text headline headline-top">
    <span class="headline-local">Local</span>
    <span class="headline-members">Members</span>
  </div>
  <div class="text headline headline-wanted">Wanted</div>

  <div class="text drill">Drill Every <span class="strong">Tuesday</span> at <span class="strong">7pm</span></div>

  <div class="text dept-name">BRACKEN MOOR</div>
  <div class="text dept-type">FIRE DEPARTMENT</div>

  <div class="text address">57 Kestrel Pond Lane</div>

  <div class="text web">www.brackenmoorfire.example</div>
</main>
</body>
</html>
```